Marvane Corvel 2008 LWB Van Wrap

- Van Wrap Design Brief for 2008 Marvane CorVel LWB
Business Type: Electronic Security
Vehicle: 2008 Marvane CorVel LWB
Purpose: Mobile branding + immediate recognition + professional authority presence on the road.

- Overview
We are designing a full van wrap for my electronic security business using my existing logo. The aim is to create a strong, attention-grabbing, and professional design that reflects trust, high-tech protection, and visual authority — something that communicates clearly even from a distance.

- Goals
Make the van a moving billboard for the brand.

Deliver a message of surveillance, protection, and cutting-edge technology.

Ensure clarity and readability — everything important must be instantly legible.

Establish a modern, powerful identity in line with the security industry.

- Design Style & Visual Elements
- Color Scheme
Use bold, high-contrast colors. I like the combination of red, black, and white for its authoritative and tech-savvy feel. You can Also use the Colours of the Logo provided. Use your creative touch!

You may explore using gradients or metallic tones for a modern finish, but keep it clean and sharp.

- Typography
Use large, strong sans-serif fonts for the business name (from the logo) and tagline.

Use smaller fonts for contact details, but ensure they’re easily readable when parked or in traffic.

-Logo Placement
Feature my logo prominently on both sides and the rear of the van. BTK ( The Ram And sheild not too BIG)

It should be the central branding element — bold, unmissable, and clean.

Avoid repeating the logo excessively — one strong presence is better than clutter.

-Imagery & Icons
Consider subtle abstract elements like:

A stylized eye or lens, representing surveillance.

Circuit patterns or digital waveforms to hint at tech/electronic focus.

But keep it minimal — this should support the logo, not overpower it.

-Layout Style
Use angled or dynamic lines to create movement and energy — it helps the van look modern and gives the illusion of motion.

Avoid boxy or traditional layouts.

Use space smartly — balance bold branding with areas of clean space to avoid clutter.

-Essential Information to Include
Business Name & Logo

Contact Number : 0462 517 308

Website URL : www.holtguardline.com.au
Email : Info@holtguardline.com.au

Optional: List of services (in short, clean bullet-point format)

💬 Tone & Personality
Professional

Tech-driven

Trustworthy

Vigilant

Modern and clean — no gimmicky effects or outdated styles

🧠 Final Thought
Use the design to make people feel watched and protected at the same time — powerful but reassuring. Think of the van not just as transport, but as an extension of the security presence. The goal is for people to instantly recognize and remember it, whether they're passing by on foot or driving behind it.
Updates

Designs look the same

Added pictures for inspiration have been uploaded.

Don't be afraid to experiment with different colours.

Please DO NOT MAKE THE RAM AND SHEILD LOGO EXTRA LARGE. It dosnt need to be so BIG. We are aiming for a professional yet eye catching design.

I have gone through most of the profiles of designers and the designs showcased on your profiles are full of creativity and professionalism, Please make this no exception. I require the same quality.

Target Market(s)

Residential - Commercial - Industrial

Industry/Entity Type

Electronic Security & Data

Colors
0094D4
00A9DD
6FCCEA
C7EBF8
E9F6FB
EB3D1F
EC4F4E
F09395
F8D3D4
FCEDEE

Requirements
Must have
• All information can be found in the Project Description
Nice to have
Should not have
• The Name BTK can be prominant. but not the Logo

```html
<!DOCTYPE html>
<html lang="en">
<head>
<meta charset="utf-8">
<title>BTK – Holt Guardline Van Wrap</title>
<link rel="stylesheet" href="https://fonts.googleapis.com/css2?family=Audiowide&family=Montserrat:wght@500;700;800&display=swap">
<style>
  :root {
    --canvas-bg: #eef0f2;
    --wrap-black: #050505;
    --body-white: #f7f7f5;
    --body-edge: #c9cbcd;
    --teal: #19c1c4;
    --silver: #d4d4d2;
    --camera-tone: #cfd1d3;
    --partner-ink: #2a2a2a;
  }
  * { margin: 0; padding: 0; box-sizing: border-box; }
  html, body {
    width: 1200px; height: 579px; overflow: hidden;
    background: var(--canvas-bg);
  }
  .wrap-canvas { position: relative; width: 1200px; height: 579px; }
  .van-side { position: absolute; inset: 0; }
  .text {
    position: absolute; white-space: nowrap; line-height: 1;
    font-family: "Montserrat", sans-serif;
  }
  .market-line {
    left: 99px; top: 123px;
    font-family: "Audiowide", sans-serif;
    font-size: 17.5px; color: var(--teal); letter-spacing: 0.4px;
  }
  .camera-lineup {
    position: absolute; left: 189px; top: 177px; width: 237px; height: 70px;
    border-radius: 35px;
    background: linear-gradient(180deg, #f2f3f4 0%, var(--camera-tone) 60%, #8d9094 100%);
  }
  .halftone-field {
    position: absolute; left: 130px; top: 325px; width: 345px; height: 165px;
    border-radius: 50% 50% 10px 10px / 60% 60% 10px 10px;
    background: radial-gradient(ellipse at 55% 40%, rgba(110,110,110,0.35) 0%, rgba(70,70,70,0.15) 55%, rgba(5,5,5,0) 80%);
  }
  .contact-phone {
    left: 243px; top: 282px;
    font-family: "Audiowide", sans-serif;
    font-size: 21px; color: var(--silver); letter-spacing: 0.8px;
  }
  .contact-email {
    left: 212px; top: 308px;
    font-size: 12px; font-weight: 500; color: var(--silver); letter-spacing: 1.5px;
  }
  .brand-mark {
    left: 524px; top: 303px;
    font-size: 74px; font-weight: 800; color: var(--silver);
    letter-spacing: 10px;
  }
  .brand-name {
    left: 526px; top: 369px;
    font-size: 24px; font-weight: 800; color: var(--teal); letter-spacing: 0.2px;
  }
  .brand-sub {
    left: 526px; top: 393px;
    font-size: 13px; font-weight: 800; color: var(--teal); letter-spacing: 0.4px;
  }
  .service-list {
    left: 526px; top: 407px;
    font-size: 8px; font-weight: 500; color: var(--silver); letter-spacing: 0.7px;
  }
  .callout {
    left: 512px; top: 436px;
    font-family: "Audiowide", sans-serif;
    font-size: 15px; color: var(--silver); letter-spacing: 0.2px;
  }
  .partner-row {
    position: absolute; left: 790px; top: 285px;
    display: flex; gap: 14px;
    font-family: "Montserrat", sans-serif;
  }
  .partner-name {
    font-size: 15px; font-weight: 700; color: var(--partner-ink); letter-spacing: 0.4px;
  }
</style>
</head>
<body>
<main class="wrap-canvas">
  <svg class="van-side" width="1200" height="579" viewBox="0 0 1200 579" aria-hidden="true">
    <path class="body-base" d="M80 76 H985 Q1010 76 1030 98 L1120 215 Q1140 235 1150 265 L1163 330 V470 Q1163 490 1143 490 H70 Q55 490 55 470 V108 Q55 76 80 76 Z"
          fill="var(--body-white)" stroke="var(--body-edge)" stroke-width="1.5"/>
    <path class="wrap-panel" d="M80 76 H605 Q640 190 730 270 Q790 325 868 372 L868 490 H70 Q55 490 55 470 V108 Q55 76 80 76 Z"
          fill="var(--wrap-black)"/>
    <path class="teal-sweep" d="M605 76 Q640 190 730 270 Q790 325 868 372"
          fill="none" stroke="var(--teal)" stroke-width="6"/>
    <path class="wheel-arch" d="M210 490 A95 95 0 0 1 400 490 Z" fill="var(--canvas-bg)"/>
    <path class="wheel-arch" d="M837 490 A95 95 0 0 1 1027 490 Z" fill="var(--canvas-bg)"/>
    <g class="icon-phone" transform="translate(229 293)">
      <circle r="9" fill="none" stroke="var(--teal)" stroke-width="2"/>
      <path d="M-4 -4 Q-5 2 1 5 L3 3 L1 1 L0 2 Q-2 0 -2 -2 L-1 -3 L-3 -5 Z" fill="var(--teal)"/>
    </g>
    <g class="icon-mail" transform="translate(198 314)">
      <circle r="8.5" fill="none" stroke="var(--teal)" stroke-width="2"/>
      <rect x="-5" y="-3.5" width="10" height="7" fill="none" stroke="var(--teal)" stroke-width="1.4"/>
      <path d="M-5 -3.5 L0 1 L5 -3.5" fill="none" stroke="var(--teal)" stroke-width="1.4"/>
    </g>
    <g class="icon-24h" transform="translate(471 445)">
      <path d="M-20 2 A20 20 0 1 0 -5 -19" fill="none" stroke="var(--teal)" stroke-width="3"/>
      <path d="M-6 -24 L4 -19 L-5 -13 Z" fill="var(--teal)"/>
      <text x="0" y="6" text-anchor="middle" font-family="Audiowide, sans-serif" font-size="14" fill="var(--teal)">24h</text>
      <line x1="-33" y1="0" x2="-27" y2="0" stroke="var(--teal)" stroke-width="1.5"/>
      <line x1="28" y1="0" x2="34" y2="0" stroke="var(--teal)" stroke-width="1.5"/>
    </g>
  </svg>

  <div class="text market-line">RESIDENTAIL - COMMERCIAL - INDUSTRIAL</div>
  <div class="camera-lineup" role="img" aria-label="Photo of a row of white security cameras: bullet and dome models"></div>
  <div class="halftone-field" role="img" aria-label="Grey halftone dot pattern fading outward"></div>
  <div class="text contact-phone">0462 517 308</div>
  <div class="text contact-email">INFO@HOLTGUARDLINE.COM.AU</div>

  <div class="text brand-mark">BTK</div>
  <div class="text brand-name">HOLT GUARDLINE</div>
  <div class="text brand-sub">&amp; CONTRACTING SOLUTIONS</div>
  <div class="text service-list">CCTV • ACCESS CONTROL • ALARMS • MONITORING</div>
  <div class="text callout">CALL OUT EMERGENCY SERVICE</div>

  <div class="partner-row">
    <span class="partner-name">KESTRON</span>
    <span class="partner-name">PALVUE</span>
    <span class="partner-name">NOXEL</span>
    <span class="partner-name">ARDENT</span>
  </div>
</main>
</body>
</html>
```